Dalvick's Business Card

I need some designs for a new business card including the new logo attached. An old example of our business card is also attached to show all the data that should be included on the new design.
**I added some more examples someone had mocked up**

Contact Information for Business Card

Should include all info on other examples uploaded.

```html
<!DOCTYPE html>
<html lang="en">
<head>
<meta charset="utf-8">
<title>Dalvick's Business Card</title>
<link href="https://fonts.googleapis.com/css2?family=Montserrat:wght@500;600;700&family=Lexend:wght@300;400&display=swap" rel="stylesheet">
<style>
  :root {
    --blue: #0b63ae;
    --blue-light: #0f78bf;
    --red: #e01f26;
    --red-soft: #d9342b;
    --card: #f7f7f7;
    --ink-white: #ffffff;
    --backdrop: #e9e9e9;
  }
  * { box-sizing: border-box; margin: 0; padding: 0; }
  html, body { width: 1200px; height: 1200px; overflow: hidden; }
  body { background: var(--backdrop); position: relative; font-family: "Lexend", sans-serif; }

  .card {
    position: absolute; left: 235px; width: 730px; height: 417px;
    background: linear-gradient(135deg, #ffffff, #ececec);
    overflow: hidden;
  }
  .card--front { top: 160px; }
  .card--back { top: 631px; }

  .brand { position: absolute; display: flex; align-items: center; }
  .brand__dot { border-radius: 50%; background: var(--red); flex: none; }
  .brand__name { font-family: "Montserrat", sans-serif; font-weight: 600; color: var(--blue); letter-spacing: 0.5px; }

  .card--front .brand { left: 50px; top: 160px; gap: 12px; }
  .card--front .brand__dot { width: 26px; height: 26px; }
  .card--front .brand__name { font-size: 38px; }

  .divider { position: absolute; left: 348px; top: 142px; width: 3px; height: 90px; background: var(--blue); }

  .contact { position: absolute; left: 380px; top: 137px; }
  .contact__name { font-family: "Montserrat", sans-serif; font-weight: 700; font-size: 31px; color: var(--red); letter-spacing: 0.3px; }
  .contact__row { display: flex; align-items: center; gap: 8px; font-weight: 300; font-size: 22px; color: var(--blue); margin-top: 6px; }
  .contact__row svg { width: 18px; height: 18px; flex: none; }

  .bands { position: absolute; left: 0; bottom: 0; width: 730px; height: 56px; }
  .band-label { position: absolute; bottom: 0; height: 56px; display: flex; align-items: center; color: var(--ink-white); font-weight: 300; font-size: 20px; letter-spacing: 0.3px; }
  .band-label--licensed { left: 52px; }
  .band-label--family { left: 384px; }

  .back-top { position: absolute; left: 0; top: 0; width: 730px; height: 90px; }
  .back-top__text { position: absolute; left: 0; top: 0; width: 730px; height: 66px; display: flex; align-items: center; justify-content: center; color: var(--ink-white); font-weight: 300; font-size: 25px; letter-spacing: 0.5px; }

  .card--back .brand { left: 0; width: 730px; top: 180px; justify-content: center; gap: 18px; }
  .card--back .brand__dot { width: 44px; height: 44px; }
  .card--back .brand__name { font-size: 66px; }

  .back-bottom { position: absolute; left: 0; bottom: 0; width: 730px; height: 89px; }
  .back-bottom__text { position: absolute; left: 0; bottom: 0; width: 730px; height: 66px; display: flex; align-items: center; justify-content: center; color: var(--ink-white); font-weight: 300; font-size: 17px; letter-spacing: 0.4px; }
</style>
</head>
<body>

<section class="card card--front">
  <div class="brand">
    <span class="brand__dot"></span>
    <span class="brand__name">DALVICK'S</span>
  </div>
  <div class="divider"></div>
  <div class="contact">
    <div class="contact__name">MARK DALVICK</div>
    <div class="contact__row">
      <svg viewBox="0 0 24 24"><path fill="var(--red)" d="M6.6 10.8a15.1 15.1 0 0 0 6.6 6.6l2.2-2.2a1 1 0 0 1 1-.25 11.4 11.4 0 0 0 3.6.57 1 1 0 0 1 1 1V20a1 1 0 0 1-1 1A17 17 0 0 1 3 4a1 1 0 0 1 1-1h3.5a1 1 0 0 1 1 1c0 1.25.2 2.45.57 3.57a1 1 0 0 1-.25 1z"/></svg>
      <span>555.014.2290</span>
    </div>
    <div class="contact__row">
      <svg viewBox="0 0 24 24"><rect x="2" y="5" width="20" height="14" rx="1.5" fill="var(--red)"/><path d="M3 6l9 7 9-7" fill="none" stroke="#fff" stroke-width="1.8"/></svg>
      <span>hvacdalvick@mail.com</span>
    </div>
  </div>

  <svg class="bands" viewBox="0 0 730 56" preserveAspectRatio="none">
    <path d="M0 0 H275 Q305 0 325 18 L357 56 H0 Z" fill="var(--blue)"/>
    <path d="M340 0 H730 V56 H373 L335 12 Q332 0 345 0 Z" fill="var(--red)"/>
  </svg>
  <div class="band-label band-label--licensed">LICENSED &amp; INSURED</div>
  <div class="band-label band-label--family">FAMILY OWNED &amp; OPERATED</div>
</section>

<section class="card card--back">
  <svg class="back-top" viewBox="0 0 730 90">
    <path d="M0 0 H730 V66 H388 L365 89 L342 66 H0 Z" fill="var(--blue)"/>
  </svg>
  <div class="back-top__text">SERVES FAIRVIEW, IA &amp; SURROUNDING AREAS</div>

  <div class="brand">
    <span class="brand__dot"></span>
    <span class="brand__name">DALVICK'S</span>
  </div>

  <svg class="back-bottom" viewBox="0 0 730 89">
    <path d="M0 23 H342 L365 0 L388 23 H730 V89 H0 Z" fill="var(--red-soft)"/>
  </svg>
  <div class="back-bottom__text">CALL TODAY FOR ALL YOUR HVAC, REFRIGERATION &amp; PLUMBING NEEDS</div>
</section>

</body>
</html>
```